Advertising Portal Needs eBrochure

Hi Crowders! Our advertising portal, which focus on the new launches property, needs an online brochure to promote to potential advertisers the benefits of advertising their projects with us. These advertisers will be mainly real estate developers and agencies.

WHAT WE LOOKING FOR
We do not want over-fanciful designs that makes the content hard to read. The use of illustrations and graphics/symbols related to covered topics are encouraged. The overall design should portrait our advertising efficiency through online and social media means. Our website - www.brightkeyhomes.sg.

For draft purposes, just do up the front page, back page, and few inner pages, preferably to include one illustration chart (either on page 7/8). Size wise probably A5 portrait or landscape, for future printing into a booklet.

WORK COMPLETION AND PAYMENT
The $500 stated here is 50% of the payment. Upon getting a desired draft design, we will need you to work on the full content with slight amendments along the way. Once done, we will be paying the balance $500, and we will need the pdf file as well as the work file.

Let your design juice flow, and hope we can work with you!
Updates

Hi Crowders! Thank you for your submissions. We are closing the project as we've decided on a design. It's a pity we can only select one design, as there are a number of good works. Hope we will have a chance to work together on our upcoming projects. Cheers =)

Target Market(s)

Real estate developers, real estate agencies, and perhaps to an extent, individual property sales agent.

Industry/Entity Type

Advertising

Requirements
Should not have
• We prefer not to have much real people kind of stock images. Try not to use images from our portal as we do not have the ownerships. Instead, you can use stock images of property developments artist impression that gives a similar feel.

```html
<!DOCTYPE html>
<html lang="en">
<head>
<meta charset="utf-8">
<title>BrightKeyHomes.sg – Advertiser Brochure Spread</title>
<link rel="stylesheet" href="https://fonts.googleapis.com/css2?family=Open+Sans:wght@400;600;700;800&display=swap">
<style>
  :root {
    --backdrop: #e7e7e5;
    --paper: #ffffff;
    --ink: #4a4a4a;
    --ink-soft: #6b6b6b;
    --green: #7ab63c;
    --green-deep: #5f9a2b;
    --charcoal-top: #55595c;
    --charcoal-bottom: #2d3033;
    --light-text: #d9dcde;
    --photo-top: #c9ced3;
    --photo-bottom: #6f757b;
  }
  * { box-sizing: border-box; margin: 0; padding: 0; }
  html, body { width: 1200px; height: 901px; overflow: hidden; }
  body {
    background: var(--backdrop);
    font-family: "Open Sans", Arial, sans-serif;
    position: relative;
  }
  .spread {
    position: absolute;
    left: 40px; top: 248px;
    width: 1120px; height: 396px;
    display: flex;
    box-shadow: 0 10px 30px rgba(0,0,0,.18);
  }
  .page { position: relative; width: 560px; height: 396px; overflow: hidden; }

  /* Left page */
  .page--left { background: var(--paper); }
  .edge-band { position: absolute; width: 16px; background: var(--green); }
  .page--left .edge-band { left: 0; top: 78px; height: 250px; }
  .hero-photo {
    position: absolute; left: 16px; top: 0; width: 220px; height: 270px;
    background: linear-gradient(180deg, var(--photo-top), var(--photo-bottom));
  }
  .intro {
    position: absolute; left: 256px; top: 30px; width: 276px;
    color: var(--ink-soft); font-size: 8.5px; line-height: 1.5;
  }
  .section-title {
    color: var(--green); font-weight: 800; font-size: 14px;
    letter-spacing: .3px; text-transform: uppercase; margin-bottom: 6px;
  }
  .intro p { margin-bottom: 8px; }
  .intro .section-title + p { margin-top: 0; }
  .intro .section-title:not(:first-child) { margin-top: 14px; }
  .closing-copy {
    position: absolute; left: 36px; top: 288px; width: 496px;
    color: var(--ink-soft); font-size: 8.5px; line-height: 1.5;
  }

  /* Right page */
  .page--right {
    background: linear-gradient(160deg, var(--charcoal-top), var(--charcoal-bottom));
    color: var(--light-text);
  }
  .page--right .edge-band { right: 0; top: 36px; height: 270px; background: var(--green); }
  .feature-heading {
    position: absolute; left: 28px; top: 24px; width: 490px;
    display: flex; align-items: center; gap: 10px;
  }
  .feature-heading h2 {
    color: #fff; font-weight: 700; font-size: 14.5px;
    text-transform: uppercase; letter-spacing: .3px;
  }
  .feature-list { position: absolute; left: 44px; top: 66px; width: 470px; }
  .feature h3 {
    color: var(--green); font-size: 9px; font-weight: 700;
    text-transform: uppercase; letter-spacing: .4px; margin-bottom: 3px;
  }
  .feature p { font-size: 8.5px; line-height: 1.5; margin-bottom: 11px; }
  .gutter {
    position: absolute; left: 556px; top: 0; width: 8px; height: 396px;
    background: linear-gradient(90deg, rgba(0,0,0,0), rgba(0,0,0,.22), rgba(0,0,0,0));
  }
</style>
</head>
<body>
  <main class="spread">
    <section class="page page--left">
      <div class="edge-band"></div>
      <div class="hero-photo" role="img" aria-label="Photo of a city skyline with high-rise towers and a waterfront, in grey tones"></div>
      <div class="intro">
        <h2 class="section-title">About BrightKeyHomes.sg</h2>
        <p>BrightKeyHomes.sg is a portal focused on new launch homes, linking buyers with the latest projects in the market.</p>
        <p>Reaching out to our growing base of buyers, we help developers and agencies present every launch clearly and quickly.</p>
        <h2 class="section-title">How are we different</h2>
        <p>When you advertise with BrightKeyHomes.sg, you are not just buying a listing. You gain a partner that plans, builds and promotes your project online.</p>
      </div>
      <p class="closing-copy">Together with our team of digital and marketing experts, we bring your launch to the right buyers through search, social media and targeted campaigns, so every enquiry counts for your company.</p>
    </section>

    <section class="page page--right">
      <div class="feature-heading">
        <svg width="22" height="22" viewBox="0 0 22 22" aria-hidden="true">
          <circle cx="11" cy="11" r="10" fill="none" stroke="#7ab63c" stroke-width="2"/>
          <path d="M6.5 11.5l3 3 6-6.5" fill="none" stroke="#7ab63c" stroke-width="2" stroke-linecap="round" stroke-linejoin="round"/>
        </svg>
        <h2>We create a full-featured webpage for your project</h2>
      </div>
      <div class="feature-list">
        <div class="feature">
          <h3>Project page</h3>
          <p>A dedicated page presents your project with photos, floor plans, pricing and key selling points in one clean layout.</p>
        </div>
        <div class="feature">
          <h3>Enquiry form</h3>
          <p>Buyers can register interest directly, and every lead is sent straight to your sales team.</p>
        </div>
        <div class="feature">
          <h3>Location and amenities</h3>
          <p>An interactive map shows nearby schools, transport and malls, helping buyers picture life at the address.</p>
        </div>
        <div class="feature">
          <h3>Social sharing</h3>
          <p>Each page can be shared across social networks with one click, extending your reach to friends and family of buyers.</p>
        </div>
        <div class="feature">
          <p>Your project page can also link to your own official site and be refreshed whenever new units are released.</p>
        </div>
      </div>
      <div class="edge-band"></div>
    </section>
    <div class="gutter"></div>
  </main>
</body>
</html>
```